MRT Property - Business Cards

Looking for a business card & general letterhead, signage etc design for our new logo.

Colours:
000a20
0056a2
00b5ef
0088ce
68cef2

Fonts:
Poppins
Karla

Please keep look and feel of new brand - example in the zip package I sent.

```html
<!DOCTYPE html>
<html lang="en">
<head>
<meta charset="utf-8">
<title>MRT Property – Business Cards</title>
<link rel="stylesheet" href="https://fonts.googleapis.com/css2?family=Poppins:wght@400;500;600;700&display=swap">
<style>
  :root {
    --ink: #000a20;
    --brand-navy: #0056a2;
    --brand-cyan: #00b5ef;
    --brand-mid: #0088ce;
    --brand-sky: #68cef2;
    --paper: #ffffff;
    --backdrop: #d6d6d6;
  }
  * { box-sizing: border-box; margin: 0; padding: 0; }
  html, body { width: 1200px; height: 711px; overflow: hidden; }
  body {
    background: var(--backdrop);
    font-family: "Poppins", sans-serif;
    color: var(--ink);
    position: relative;
  }
  .card {
    position: absolute;
    top: 197px;
    width: 520px;
    height: 317px;
    background: var(--paper);
    box-shadow: 0 6px 18px rgba(0, 0, 0, 0.18);
  }
  .card--contact { left: 60px; }
  .card--brand { left: 620px; display: flex; align-items: center; justify-content: center; }

  .wordmark {
    display: flex;
    align-items: center;
    gap: 10px;
    color: var(--brand-navy);
    font-weight: 700;
    white-space: nowrap;
  }
  .wordmark__dot {
    border-radius: 50%;
    background: var(--brand-sky);
    flex: none;
  }
  .wordmark--small { font-size: 24px; gap: 8px; }
  .wordmark--small .wordmark__dot { width: 18px; height: 18px; }
  .wordmark--large { font-size: 58px; gap: 16px; }
  .wordmark--large .wordmark__dot { width: 40px; height: 40px; }

  .card--contact .wordmark {
    position: absolute;
    left: 30px;
    top: 92px;
    width: 220px;
  }
  .divider {
    position: absolute;
    left: 270px;
    top: 50px;
    width: 1px;
    height: 170px;
    background: var(--brand-mid);
  }
  .person {
    position: absolute;
    left: 296px;
    top: 78px;
  }
  .person__name {
    font-size: 28px;
    line-height: 1.1;
    font-weight: 700;
    color: var(--brand-navy);
  }
  .person__surname {
    font-weight: 400;
    color: var(--brand-sky);
  }
  .person__role {
    font-size: 13px;
    font-weight: 600;
    color: var(--ink);
    margin-top: 2px;
  }
  .contact-list {
    list-style: none;
    margin-top: 16px;
    font-size: 12px;
    line-height: 1.6;
  }
  .contact-list li { display: flex; align-items: center; gap: 8px; }
  .contact-list svg { width: 12px; height: 12px; flex: none; }
  .address {
    position: absolute;
    left: 34px;
    bottom: 26px;
    font-size: 12px;
    color: var(--ink);
    white-space: nowrap;
  }
</style>
</head>
<body>
  <section class="card card--contact">
    <div class="wordmark wordmark--small"><span class="wordmark__dot"></span>MRT Property</div>
    <div class="divider"></div>
    <div class="person">
      <p class="person__name">Callum <span class="person__surname">Reid</span></p>
      <p class="person__role">Director</p>
      <ul class="contact-list">
        <li>
          <svg viewBox="0 0 24 24" aria-hidden="true"><path fill="#68cef2" d="M6.6 10.8a15.1 15.1 0 0 0 6.6 6.6l2.2-2.2c.3-.3.7-.4 1-.2 1.1.4 2.300.6 3.600.6.6 0 1 .4 1 1V20c0 .6-.4 1-1 1A17 17 0 0 1 3 4c0-.6.4-1 1-1h3.5c.6 0 1 .4 1 1 0 1.3.2 2.5.6 3.6.1.3 0 .7-.2 1z"/></svg>
          +61 2 9000 1234
        </li>
        <li>
          <svg viewBox="0 0 24 24" aria-hidden="true"><circle cx="12" cy="12" r="9" fill="none" stroke="#68cef2" stroke-width="2"/><path d="M3 12h18M12 3c3 3 3 15 0 18M12 3c-3 3-3 15 0 18" fill="none" stroke="#68cef2" stroke-width="1.6"/></svg>
          www.mrtproperty.com.au
        </li>
        <li>
          <svg viewBox="0 0 24 24" aria-hidden="true"><rect x="2" y="5" width="20" height="14" rx="2" fill="none" stroke="#68cef2" stroke-width="2"/><path d="M3 6l9 7 9-7" fill="none" stroke="#68cef2" stroke-width="2"/></svg>
          info@mrtproperty.com.au
        </li>
      </ul>
    </div>
    <p class="address">Suite 4.12, Level 4 18 Harbour Lane Riverton NSW 2100</p>
  </section>

  <section class="card card--brand">
    <div class="wordmark wordmark--large"><span class="wordmark__dot"></span>MRT Property</div>
  </section>
</body>
</html>
```